Packaging and Insert Design for New Cocktail/Bar Set

We are launching a new product under our brand, Shaker Haven, and require a design for the product packaging (2 packages - an inner cylinder tube and an outer box), as well as an insert.

(Note for reference - "mixology" is the art of cocktail making).

Our product is a cocktail set which will be sold on the USA Amazon site.

Our logo has already been designed - please refer to the attached files. I've attached various vector files of our logo.

The cocktail set will be packaged in a cylinder tube box.
Please see uploaded files for an image of the cylinder, as well as dimensions.
Dimensions are 37.68cm x 28cm (when the print design is laid flat).
The physical tube will be 28cm high and have a diameter of 12cm.
See uploaded file 'Dimensions - Cylinder Box' for details.

The cylinder box will be enclosed in an outer white box for protection. The outer white box will be a very basic box (i.e. not high quality) we are using just to make storage of individual units easier (and to protect the cylinder tube). It is unlikely that the outer box will be retained by the buyer. It will have a very clean, simple design. It will have our logo on the front and a barcode on the back (at the bottom).
Dimensions of the outer box are 28.5cm high and 12.5cm wide (tall and rectangular in shape).
See uploaded file 'Dimensions - White Outer Box & Paper Card' for details.

So to confirm we have 2 packages - the internal cylinder tube will have full branding, and this will then be placed in the white outer box with a simple design (logo only plus barcode at the back).

We also require a small insert to be designed (9.1cm x 5.5cm). We will include the insert in the package. The insert will have our logo and will provide the buyer with our contact details. The buyer will register their email address with us, in order to quality for warranty and a free e-book.

We need to finalise the content for the product insert, as well as the additional information to be printed on the cylinder tube.

In terms of design for the inner cylinder tube, we are leaning towards a more simple design, with our logo displayed on the front of the box.
We are open to ideas/suggestions though.

We have also uploaded an image of the cocktail set components which will form part of the set.

Target Market(s)

Our target market will be cocktail making enthusiasts/hobbyists and professionals. This includes people who would like to but a cocktail set to use at home, as well as professional bartenders.

Industry/Entity Type

Product

Colors

Designer to choose colors to be used in the design.

Requirements
Must have
• Preference is for a clean, professional looking design.
• Internal cylinder tube - full branding, incorporating logo on the front. Possibly also either a slogan e.g. "The Art of Cocktail Making' or details of the product e.g. "Cocktail Making Set' or similar.
• Outer white box - very simple design with logo to be displayed on the front of the packaging.
Should not have
• The design should not be too busy/complex. Not too much going on.

```html
<!DOCTYPE html>
<html lang="en">
<head>
<meta charset="utf-8">
<title>Shaker Haven – Cylinder Tube Label Concepts</title>
<link href="https://fonts.googleapis.com/css2?family=Cinzel:wght@400;500&family=Oswald:wght@500&display=swap" rel="stylesheet">
<style>
  :root {
    --bg: #e6e6e6;
    --black: #060606;
    --navy-top: #1d3450;
    --navy-bottom: #243e5c;
    --silver-light: #f4f4f4;
    --silver-mid: #c9c9c9;
    --silver-dark: #8c8c8c;
    --steel-dark: #3a3a3a;
    --steel-mid: #6b6b6b;
    --text-silver: #e9e9e9;
  }
  * { margin: 0; padding: 0; box-sizing: border-box; }
  html, body { width: 1200px; height: 1200px; overflow: hidden; }
  body { background: var(--bg); position: relative; font-family: "Cinzel", serif; }

  .label { position: absolute; overflow: hidden; }
  .label svg.art { position: absolute; inset: 0; }
  .label .copy { position: absolute; left: 0; right: 0; text-align: center; color: var(--text-silver); }

  .brand-name {
    font-family: "Cinzel", serif;
    font-weight: 500;
    color: var(--text-silver);
    letter-spacing: 0.22em;
    text-transform: uppercase;
  }

  /* Concept 1: black with steel chevrons */
  .label--steel { left: 96px; top: 392px; width: 216px; height: 480px; background: var(--black); }
  .label--steel .brand-name { position: absolute; top: 160px; left: 0; right: 0; text-align: center; font-size: 15px; }
  .label--steel .product { top: 228px; font-size: 15px; line-height: 1.15; }
  .label--steel .product .big { font-size: 24px; display: block; }

  /* Concept 2: black with diagonal stripes */
  .label--stripe { left: 460px; top: 368px; width: 280px; height: 592px; background: var(--black); }
  .label--stripe .brand-name { position: absolute; top: 160px; left: 0; right: 0; text-align: center; font-size: 21px; }
  .label--stripe .product { top: 222px; font-family: "Oswald", sans-serif; font-weight: 500; line-height: 1; }
  .label--stripe .product .line1 { display: block; font-size: 36px; padding-bottom: 8px; }
  .label--stripe .product .rule { display: block; height: 1px; background: var(--silver-dark); margin: 0 12px 8px; }
  .label--stripe .product .line2 { display: block; font-size: 36px; }

  /* Concept 3: navy banner */
  .label--navy { left: 884px; top: 384px; width: 228px; height: 496px; background: linear-gradient(180deg, var(--navy-top), var(--navy-bottom)); }
  .label--navy .brand-name { position: absolute; top: 212px; left: 0; right: 0; text-align: center; font-size: 15px; }
  .label--navy .product { top: 264px; font-size: 16px; line-height: 1.15; }
  .label--navy .product .big { font-size: 25px; display: block; }
</style>
</head>
<body>

  <section class="label label--steel">
    <svg class="art" width="216" height="480" viewBox="0 0 216 480">
      <defs>
        <linearGradient id="steelA" x1="0" y1="0" x2="1" y2="1">
          <stop offset="0" stop-color="#7a7a7a"/><stop offset="0.5" stop-color="#4a4a4a"/><stop offset="1" stop-color="#6e6e6e"/>
        </linearGradient>
        <linearGradient id="steelB" x1="1" y1="0" x2="0" y2="1">
          <stop offset="0" stop-color="#9a9a9a"/><stop offset="0.6" stop-color="#5c5c5c"/><stop offset="1" stop-color="#3c3c3c"/>
        </linearGradient>
      </defs>
      <rect x="0" y="312" width="216" height="168" fill="#4c4c4c"/>
      <polygon points="0,312 108,372 216,312 216,350 108,412 0,350" fill="url(#steelA)"/>
      <polygon points="0,350 108,412 216,350 216,395 108,452 0,395" fill="url(#steelB)"/>
      <polygon points="0,395 108,452 216,395 216,480 0,480" fill="#3e3e3e"/>
      <polyline points="0,312 108,372 216,312" fill="none" stroke="#a8a8a8" stroke-width="1"/>
      <polyline points="0,350 108,412 216,350" fill="none" stroke="#9a9a9a" stroke-width="1"/>
    </svg>
    <div class="brand-name">Shaker Haven</div>
    <p class="copy product">Stainless Steel<span class="big">Cocktail</span>Shaker Set</p>
  </section>

  <section class="label label--stripe">
    <svg class="art" width="280" height="592" viewBox="0 0 280 592">
      <defs>
        <linearGradient id="silver" x1="0" y1="0" x2="1" y2="1">
          <stop offset="0" stop-color="#f6f6f6"/><stop offset="0.5" stop-color="#d4d4d4"/><stop offset="1" stop-color="#a8a8a8"/>
        </linearGradient>
        <clipPath id="stripeZone">
          <polygon points="0,344 0,592 124,592 124,344"/>
        </clipPath>
      </defs>
      <polygon points="280,344 280,592 12,592" fill="url(#silver)"/>
      <g clip-path="url(#stripeZone)" stroke="#cfcfcf" stroke-width="9">
        <line x1="0" y1="360" x2="150" y2="510"/>
        <line x1="0" y1="385" x2="150" y2="535"/>
        <line x1="0" y1="410" x2="150" y2="560"/>
        <line x1="0" y1="435" x2="150" y2="585"/>
        <line x1="0" y1="460" x2="150" y2="610"/>
        <line x1="0" y1="485" x2="150" y2="635"/>
        <line x1="0" y1="510" x2="150" y2="660"/>
        <line x1="0" y1="535" x2="150" y2="685"/>
        <line x1="0" y1="560" x2="150" y2="710"/>
      </g>
      <polygon points="280,344 12,592 0,592 0,592" fill="none"/>
      <polygon points="124,344 280,344 12,592" fill="var(--black)" opacity="0"/>
    </svg>
    <div class="brand-name">Shaker Haven</div>
    <p class="copy product"><span class="line1">Stainless Steel</span><span class="rule"></span><span class="line2">Cocktail Shaker Set</span></p>
  </section>

  <section class="label label--navy">
    <svg class="art" width="228" height="496" viewBox="0 0 228 496">
      <defs>
        <linearGradient id="silverNavy" x1="0" y1="0" x2="1" y2="0">
          <stop offset="0" stop-color="#c4c4c4"/><stop offset="0.45" stop-color="#f7f7f7"/><stop offset="1" stop-color="#b5b5b5"/>
        </linearGradient>
      </defs>
      <rect x="0" y="120" width="228" height="7" fill="url(#silverNavy)"/>
      <rect x="0" y="133" width="228" height="2" fill="url(#silverNavy)"/>
      <polygon points="0,356 114,400 228,356 228,496 0,496" fill="url(#silverNavy)"/>
    </svg>
    <div class="brand-name">Shaker Haven</div>
    <p class="copy product">Stainless Steel<span class="big">Cocktail</span>Shaker Set</p>
  </section>

</body>
</html>
```